Marcus Delbridge Finance

Need a personal website advertising Equipment Finance,Business Finance,Commercial Finance, Construction Finance, Bridging Finance. Similar websites are www.corvalend.com.au / www.tarmivest.com.au / www.qbr7.com.au /wwwhalvecredit.com.au

Target Market(s)

Business People

Industry/Entity Type

Business

Number of Pages Required

3 page

Font styles to use
Serif
Sans Serif

Requirements
Must have
• All i want is a simple corporate looking website advertising Equipment Finance, Commercial Finance, Construction Finance, Business Finance, Bridging Finance,

```html
<!DOCTYPE html>
<html lang="en">
<head>
<meta charset="utf-8">
<title>Marcus Delbridge Finance</title>
<link rel="stylesheet" href="https://fonts.googleapis.com/css2?family=Mulish:wght@300;400;600&family=Open+Sans:ital,wght@0,400;0,600;1,400&display=swap">
<style>
:root{
  --blue:#3ea9df;
  --blue-footer:#44ade1;
  --orange:#ff8a00;
  --ink:#2b2b2b;
  --grey-text:#666;
  --grey-light:#f3f3f3;
  --navy:#0f3552;
  --line:#e2e2e2;
  --white:#fff;
  --dark-btn:#3a3a3a;
}
*{margin:0;padding:0;box-sizing:border-box}
html,body{width:1200px;height:2571px;overflow:hidden;background:var(--white)}
body{position:relative;font-family:"Open Sans",sans-serif;color:var(--ink)}

/* header */
.site-header{position:absolute;left:0;top:0;width:1200px;height:98px;background:var(--white)}
.brand{position:absolute;left:120px;top:32px;font-family:"Mulish",sans-serif;font-size:25px;color:var(--blue);font-weight:400}
.main-nav{position:absolute;left:448px;top:38px;display:flex;gap:27px;font-family:"Mulish",sans-serif;font-size:17px;color:#555}
.nav-phone{position:absolute;left:916px;top:34px;font-family:"Mulish",sans-serif;font-size:18px;color:#555;display:flex;align-items:center;gap:6px}

/* hero */
.hero{position:absolute;left:0;top:98px;width:1200px;height:545px;background:linear-gradient(160deg,#6f8594 0%,#9fb2bf 40%,#d9e2e8 62%,#8da1ae 80%,#5e7382 100%)}
.hero-kicker{position:absolute;left:118px;top:246px;font-family:"Mulish",sans-serif;font-size:22px;color:var(--white);letter-spacing:.5px}
.hero-title{position:absolute;left:118px;top:278px;font-family:"Mulish",sans-serif;font-size:40px;color:var(--white);font-weight:600}
.quote-box{position:absolute;left:767px;top:125px;width:311px;height:280px;background:var(--orange);padding:26px 26px}
.quote-box h2{font-family:"Mulish",sans-serif;font-weight:400;font-size:26px;color:var(--white)}
.quote-box p{font-size:12.5px;color:#ffe6c8;line-height:18px;margin-top:6px}
.quote-field{width:266px;height:36px;background:var(--white);margin-top:14px;font-size:12px;color:#aaa;padding:10px 14px}
.quote-field + .quote-field{margin-top:8px}
.quote-submit{width:128px;height:40px;background:var(--dark-btn);color:var(--white);font-family:"Mulish",sans-serif;font-size:17px;text-align:center;line-height:40px;margin-top:12px}
.slider-dots{position:absolute;left:551px;top:508px;display:flex;gap:8px}
.slider-dots span{width:14px;height:14px;border-radius:50%;background:var(--white);border:2px solid var(--white)}
.slider-dots span.active{background:transparent}

/* services */
.section-title{position:absolute;width:1200px;text-align:center;font-family:"Mulish",sans-serif;font-weight:400;font-size:28px;color:#222}
.title-rule{position:absolute;top:702px;height:1px;width:52px;background:#bbb}
.service{position:absolute;top:782px;width:186px;height:158px;text-align:center}
.service-icon{height:72px;margin-top:22px;margin-bottom:10px;display:flex;align-items:center;justify-content:center}
.service span{font-family:"Mulish",sans-serif;font-size:17px;color:#444;line-height:22px;display:block}
.service-divider{position:absolute;top:782px;width:1px;height:158px;background:var(--line)}

/* about */
.about{position:absolute;left:0;top:1034px;width:1200px;height:432px;background:var(--grey-light)}
.about-photo{position:absolute;left:560px;top:0;width:640px;height:432px;background:linear-gradient(90deg,rgba(243,243,243,1) 0%,#dfe6ec 30%,#b9c9d6 60%,#8fa9c0 100%)}
.about h2{position:absolute;left:128px;top:78px;font-family:"Mulish",sans-serif;font-weight:400;font-size:29px;color:#333}
.about p{position:absolute;left:128px;width:480px;font-size:13px;line-height:21px;color:#666}
.btn{position:absolute;height:40px;border-radius:20px;color:var(--white);font-size:13px;text-align:center;line-height:40px;text-transform:uppercase}
.btn-orange{background:var(--orange)}
.btn-blue{background:var(--blue)}

/* cards band */
.band{position:absolute;left:0;top:1466px;width:1200px;height:375px;background:linear-gradient(90deg,#103a5a,#0d2f4a 60%,#163f60)}
.card{position:absolute;top:58px;width:470px;height:243px;background:var(--white);overflow:hidden}
.card-photo{position:absolute;left:0;top:0;width:250px;height:243px;clip-path:polygon(0 0,85% 0,100% 100%,0 100%)}
.card h3{position:absolute;left:264px;top:24px;font-family:"Mulish",sans-serif;font-weight:400;font-size:22px}
.card p{position:absolute;left:264px;width:190px;font-size:12.5px;line-height:19px;color:#555}
.card .btn{left:264px;top:180px;width:112px;height:32px;line-height:32px;font-size:11px;border-radius:16px}

/* testimonial */
.avatar{position:absolute;border-radius:50%;background:#c9c9c9;border:3px solid var(--white);box-shadow:0 0 0 1px #ddd}
.testimonial-box{position:absolute;left:308px;top:1988px;width:593px;height:190px;border:1px solid #e6e6e6;background:var(--white)}
.testimonial-box blockquote{position:absolute;left:20px;top:56px;width:553px;text-align:center;font-style:italic;font-size:14.5px;line-height:26px;color:#555}
.author{position:absolute;width:593px;top:116px;text-align:center;font-size:15px;color:var(--blue)}
.stars{position:absolute;width:593px;top:140px;text-align:center;color:var(--orange);font-size:20px;letter-spacing:2px}
.arrow{position:absolute;top:2052px}

/* footer */
.site-footer{position:absolute;left:0;top:2228px;width:1200px;height:343px;background:var(--blue-footer);color:var(--white)}
.foot-col{position:absolute;top:46px}
.foot-col h4{font-family:"Mulish",sans-serif;font-weight:400;font-size:22px;margin-bottom:14px}
.foot-col li{list-style:none;font-size:12.5px;line-height:29px}
.foot-col.contact li{line-height:25px}
.social{display:flex;gap:6px}
.social span{width:30px;height:30px;border-radius:50%;border:2px solid var(--white)}
.foot-rule{position:absolute;left:140px;top:268px;width:940px;height:1px;background:rgba(255,255,255,.35)}
.copyright{position:absolute;width:1200px;top:294px;text-align:center;font-size:13px;color:#e4f3fb}
</style>
</head>
<body>

<header class="site-header">
  <div class="brand">Marcus Delbridge Finance</div>
  <nav class="main-nav"><span>About</span><span>Financing Services</span><span>How it works</span><span>Support</span></nav>
  <div class="nav-phone">
    <svg width="20" height="20" viewBox="0 0 24 24"><path fill="#3ea9df" d="M6.6 10.8a15.1 15.1 0 0 0 6.6 6.6l2.2-2.2a1 1 0 0 1 1-.25 11.4 11.4 0 0 0 3.6.6 1 1 0 0 1 1 1V20a1 1 0 0 1-1 1A17 17 0 0 1 3 4a1 1 0 0 1 1-1h3.5a1 1 0 0 1 1 1c0 1.25.2 2.450.6 3.6a1 1 0 0 1-.25 1z"/></svg>
    61 7 5550 1234
  </div>
</header>

<section class="hero" role="img" aria-label="Steel arch bridge over a highway at dawn">
  <div class="hero-kicker">FUSCE ULTRICIES ORCI FEUGIAT</div>
  <h1 class="hero-title">COMMERCIAL FINANCE</h1>
  <form class="quote-box">
    <h2>Get a Quote Now</h2>
    <p>Class aptent taciti sociosqu ad litora torquent per conubia nost</p>
    <div class="quote-field">Name</div>
    <div class="quote-field">Email address</div>
    <div class="quote-submit">Submit</div>
  </form>
  <div class="slider-dots"><span class="active"></span><span></span><span></span><span></span></div>
</section>

<div class="title-rule" style="left:374px"></div>
<h2 class="section-title" style="top:684px">What Services we provide</h2>
<div class="title-rule" style="left:774px"></div>

<div class="service" style="left:128px">
  <div class="service-icon"><svg width="56" height="48" viewBox="0 0 56 48"><rect x="4" y="12" width="48" height="32" rx="3" fill="#3ea9df"/><rect x="20" y="4" width="16" height="10" rx="2" fill="none" stroke="#3ea9df" stroke-width="3"/><rect x="4" y="24" width="48" height="2" fill="#fff"/><rect x="25" y="21" width="6" height="8" fill="#fff"/></svg></div>
  <span>Business<br>Finance</span>
</div>
<div class="service-divider" style="left:312px"></div>
<div class="service" style="left:313px">
  <div class="service-icon"><svg width="70" height="66" viewBox="0 0 70 66" fill="none" stroke="#3ea9df" stroke-width="2.4"><rect x="8" y="4" width="30" height="54" rx="6"/><rect x="14" y="24" width="20" height="14"/><path d="M38 26h14v12H38M52 30h10v4H52"/><path d="M14 12h18M14 48h18"/></svg></div>
  <span>Equipment<br>Finance</span>
</div>
<div class="service-divider" style="left:493px"></div>
<div class="service" style="left:499px">
  <div class="service-icon"><svg width="70" height="66" viewBox="0 0 70 66" fill="#3ea9df"><rect x="6" y="20" width="18" height="44"/><rect x="26" y="4" width="20" height="60"/><rect x="48" y="26" width="16" height="38"/><g fill="#fff"><rect x="30" y="10" width="4" height="5"/><rect x="38" y="10" width="4" height="5"/><rect x="30" y="22" width="4" height="5"/><rect x="38" y="22" width="4" height="5"/><rect x="10" y="28" width="4" height="5"/><rect x="16" y="28" width="4" height="5"/><rect x="52" y="34" width="4" height="5"/><rect x="32" y="50" width="8" height="14"/></g></svg></div>
  <span>Commercial<br>Finance</span>
</div>
<div class="service-divider" style="left:680px"></div>
<div class="service" style="left:684px">
  <div class="service-icon"><svg width="70" height="68" viewBox="0 0 70 68" fill="none" stroke="#3ea9df" stroke-width="2.4"><path d="M14 44V10L40 4v8M14 10l36 6M14 22l20-14"/><path d="M40 12v10"/><circle cx="40" cy="26" r="3"/><rect x="10" y="44" width="44" height="10" fill="#3ea9df"/><rect x="8" y="56" width="50" height="10" rx="5"/><circle cx="16" cy="61" r="2" fill="#3ea9df"/><circle cx="28" cy="61" r="2" fill="#3ea9df"/><circle cx="40" cy="61" r="2" fill="#3ea9df"/><circle cx="50" cy="61" r="2" fill="#3ea9df"/></svg></div>
  <span>Construction<br>Finance</span>
</div>
<div class="service-divider" style="left:868px"></div>
<div class="service" style="left:868px">
  <div class="service-icon"><svg width="82" height="50" viewBox="0 0 82 50" fill="none" stroke="#3ea9df" stroke-width="2.6"><path d="M2 40h78M6 40V22M76 40V22M6 22q35-22 70 0"/><path d="M18 40V14M30 40V8M41 40V6M52 40V8M64 40V14"/><path d="M2 28h78"/></svg></div>
  <span>Bridging<br>Finance</span>
</div>

<section class="about">
  <div class="about-photo" role="img" aria-label="Businessman reviewing documents at a laptop in a bright office"></div>
  <h2>Do You Want Start a Business?</h2>
  <p style="top:136px">Mr. Marcus Delbridge serves as Operations Director of Halvern Financial Services Pty Ltd. Mr. Delbridge has 16 years experience in the Financial Services and bridging Finance industry, both in Australia, as well as in South Africa. He was employed by the South African based business (SOUTHGATE FINANCE) for the majority of its operation.</p>
  <p style="top:250px">He held senior operational positions within Southgate Finance and provided staff support and direction, training and operational</p>
  <div class="btn btn-orange" style="left:128px;top:310px;width:134px">Read More</div>
</section>

<section class="band" role="img" aria-label="Dark blue tinted building under construction">
  <article class="card" style="left:120px">
    <div class="card-photo" role="img" aria-label="Team of colleagues meeting around a table" style="background:linear-gradient(135deg,#c9b39c,#8f7a66 60%,#d8d2c8)"></div>
    <h3 style="color:var(--blue)">Our Team</h3>
    <p style="top:66px">Praesent elementum elit at tellus nec ultricies sit</p>
    <p style="top:114px">Amet porttitor mattis enim In massa libero interdum nec interdum vel blandit</p>
    <div class="btn btn-blue">Read More</div>
  </article>
  <article class="card" style="left:601px">
    <div class="card-photo" role="img" aria-label="Concrete building frame under construction with a crane" style="background:linear-gradient(160deg,#9fc0e0,#b9a38a 55%,#6e5c4a)"></div>
    <h3 style="color:var(--orange)">Get Finance Now</h3>
    <p style="top:66px">Praesent elementum elit at tellus nec ultricies sit</p>
    <p style="top:114px">Amet porttitor mattis enim In massa libero interdum nec interdum vel blandit</p>
    <div class="btn btn-orange">Read More</div>
  </article>
</section>

<h2 class="section-title" style="top:1890px">Testimonial</h2>
<div class="testimonial-box">
  <blockquote>Aommodo a mi Morbi ornare gravida elit Integer congue augue et malesuada iaculis ipsum dui aliquet felis at cursus magna</blockquote>
  <div class="author">By Author Name</div>
  <div class="stars">★★★★</div>
</div>
<div class="avatar" role="img" aria-label="Client portrait" style="left:496px;top:1958px;width:62px;height:62px;background:#b5b5b5"></div>
<div class="avatar" role="img" aria-label="Client portrait" style="left:644px;top:1958px;width:62px;height:62px;background:#bdbdbd"></div>
<div class="avatar" role="img" aria-label="Featured client portrait" style="left:557px;top:1936px;width:90px;height:90px;background:#a89888"></div>
<svg class="arrow" style="left:262px" width="22" height="36" viewBox="0 0 22 36"><path d="M18 2 4 18l14 16" fill="none" stroke="#aaa" stroke-width="3"/></svg>
<svg class="arrow" style="left:920px" width="22" height="36" viewBox="0 0 22 36"><path d="M4 2l14 16L4 34" fill="none" stroke="#aaa" stroke-width="3"/></svg>

<footer class="site-footer">
  <div class="foot-col" style="left:149px"><h4>Company</h4><ul><li>About Us</li><li>Why We Are</li><li>How it Works</li><li>Support</li></ul></div>
  <div class="foot-col" style="left:320px"><h4>Services</h4><ul><li>Equipment Finance</li><li>Business Finance</li><li>Commercial Finance</li><li>Construction Finance</li><li>Bridging Finance</li></ul></div>
  <div class="foot-col" style="left:515px"><h4>Resources</h4><ul><li>Support</li><li>FAQ</li><li>Testimonials</li><li>Contact Us</li></ul></div>
  <div class="foot-col contact" style="left:685px"><h4>Contact Us</h4><ul><li>12 Harbour Lane</li><li>Coral Bay, Queensland 4999</li><li>Australia</li><li>Phone: 61 7 5550 1234</li><li>Fax: 61 7 5550 1299</li></ul></div>
  <div class="foot-col" style="left:943px"><h4>Follow Us</h4><div class="social"><span></span><span></span><span></span><span></span></div></div>
  <div class="foot-rule"></div>
  <div class="copyright">© 2017 Company Name &nbsp;All right reserved &nbsp;Term of Use</div>
</footer>

</body>
</html>
```